Business Card Design Project

We are looking to redesign the logo, business card and stationary of one of our group companies - SOLARO SUPPLY HOUSE LLC.

The company specialises in industrial PVC and CPVC Piping systems. It is situated in the Middle East and the focus is purely in this region.

The logo work is already completed. The file is uploaded for the reference.

We are looking for a clean minimalistic design for the business card.

regards
Rohit
Updates

Hello Everyone!

Thanks for submitting your designs. 

Yet to find the right design. Probably the below links will give you guys some more idea on what we would like.

Minimalist design with some creativity.

Rohit

http://exampledesignfolio.com/inspiration/15-beautifully-minimal-business-cards

http://www.samplelayoutbase.com/2011/11/14/30-minimalist-business-card-design/

http://www.primepixelcraft.com/inspiration/minimal-business-cards/

Target Market(s)

Industrial users

Industry/Entity Type

Industrial

Requirements
Must have
• - Minimalistic design

- Back side of the card should include the manufacturer PIPEMARQ NORTHERN's decal. The file is upload for the reference

- Further information
Company Name:
SOLARO SUPPLY HOUSE LLC
Address:
PO Box 8152, Sharjah Industrial Area 4, Qarwan Road
Sharjah, United Arab Emirates
Telephone:
+971-6-5000-118
Fax:
+977-6-5000-119
Email:
mail@sshlexample.com

- FYI, Solaro Supply House LLC is the authorised distributor for PIPEMARQ NORTHERN in the UAE. For further information on pipemarq please visit the website www.pipemarq-example.ca

```html
<!DOCTYPE html>
<html lang="en">
<head>
<meta charset="utf-8">
<title>Solaro Supply House – Business Card</title>
<link href="https://fonts.googleapis.com/css2?family=Questrial&family=Montserrat:wght@400;600&display=swap" rel="stylesheet">
<style>
  :root {
    --page-bg: #d9dde1;
    --card-center: #1f3d66;
    --card-mid: #0f2040;
    --card-edge: #060b18;
    --accent-blue: #8fb4ea;
    --label-blue: #6fa0e0;
    --text-white: #f2f5fa;
    --text-soft: #c9d3e3;
    --mark-fill: #3c6fb3;
  }
  * { box-sizing: border-box; margin: 0; padding: 0; }
  html, body { width: 1200px; height: 828px; overflow: hidden; }
  body {
    background: var(--page-bg);
    display: flex;
    flex-direction: column;
    align-items: center;
    justify-content: center;
    gap: 40px;
    font-family: "Montserrat", Arial, sans-serif;
  }
  .card {
    position: relative;
    width: 640px;
    height: 366px;
    border-radius: 4px;
    background: radial-gradient(ellipse at 48% 40%, var(--card-center) 0%, var(--card-mid) 45%, var(--card-edge) 100%);
    box-shadow: 0 6px 18px rgba(0, 0, 0, 0.25);
    overflow: hidden;
  }

  /* Front */
  .front-identity {
    position: absolute;
    top: 78px;
    left: 0;
    width: 100%;
    text-align: center;
  }
  .company-mark {
    display: block;
    width: 62px;
    height: 62px;
    margin: 0 auto 18px;
    border-radius: 14px;
    background: var(--mark-fill);
    border: 5px solid #2a2f3a;
  }
  .company-name {
    font-family: "Questrial", "Century Gothic", sans-serif;
    font-size: 33px;
    letter-spacing: 1px;
    color: var(--accent-blue);
    font-weight: 400;
  }
  .product-line {
    margin-top: 12px;
    font-size: 13px;
    font-weight: 600;
    letter-spacing: 1.6px;
    color: var(--text-white);
  }

  /* Manufacturer decal */
  .maker-decal {
    position: absolute;
    right: 26px;
    bottom: 24px;
    display: flex;
    align-items: center;
    gap: 8px;
  }
  .maker-dot {
    width: 34px;
    height: 34px;
    border-radius: 50%;
    background: var(--mark-fill);
    border: 2px solid var(--text-white);
  }
  .maker-name {
    font-size: 15px;
    font-weight: 600;
    line-height: 1.05;
    color: var(--text-white);
  }

  /* Back */
  .back-details {
    position: absolute;
    top: 118px;
    left: 150px;
    display: flex;
    gap: 14px;
  }
  .person {
    text-align: right;
    padding-top: 2px;
  }
  .person-name {
    font-size: 17px;
    font-weight: 600;
    letter-spacing: 1.5px;
    color: var(--text-white);
  }
  .person-role {
    font-size: 9px;
    letter-spacing: 1px;
    color: var(--text-soft);
  }
  .divider {
    width: 1px;
    height: 100px;
    background: var(--text-soft);
    opacity: 0.7;
  }
  .contact {
    font-size: 10.5px;
    line-height: 1.6;
    letter-spacing: 0.4px;
    color: var(--text-white);
  }
  .contact .firm { color: var(--label-blue); font-weight: 600; letter-spacing: 1px; }
  .contact .label { color: var(--label-blue); }
</style>
</head>
<body>
  <section class="card card-front">
    <div class="front-identity">
      <span class="company-mark" aria-hidden="true"></span>
      <h1 class="company-name">SOLARO SUPPLY HOUSE</h1>
      <p class="product-line">PIPES | FITTINGS | VALVES | ACCESSORIES</p>
    </div>
    <div class="maker-decal">
      <span class="maker-dot" aria-hidden="true"></span>
      <span class="maker-name">Pipemarq<br>Northern</span>
    </div>
  </section>

  <section class="card card-back">
    <div class="back-details">
      <div class="person">
        <p class="person-name">MARK ELLIS</p>
        <p class="person-role">head of marketing</p>
      </div>
      <span class="divider" aria-hidden="true"></span>
      <div class="contact">
        <p class="firm">SOLARO SUPPLY HOUSE LLC</p>
        <p>PO Box 8152, Sharjah Industrial Area 4, Qarwan Road</p>
        <p>Sharjah, United Arab Emirates</p>
        <p><span class="label">Telephone:</span> +971-6-5000-118</p>
        <p><span class="label">Fax:</span> +977-6-5000-119</p>
        <p><span class="label">Email:</span> mail@sshlexample.com</p>
      </div>
    </div>
    <div class="maker-decal">
      <span class="maker-dot" aria-hidden="true"></span>
      <span class="maker-name">Pipemarq<br>Northern</span>
    </div>
  </section>
</body>
</html>
```